Business Cards for a law firm

Business cards for our law firm. Use our silhoette logo and OAK PARTNERS - check our website (www.oakpartners.example)

Contact Information for Business Card

our silhouette logo, OAK PARTNERS, 800-555-0147, Dorian Pemberton, dorian@oakpartners.example

Requirements
Must have
• our silhouette logo, OAK PARTNERS, 800-555-0147, Dorian Pemberton, dorian@oakpartners.example

```html
<!DOCTYPE html>
<html lang="en">
<head>
<meta charset="utf-8">
<title>Oak Partners – Business Cards</title>
<link href="https://fonts.googleapis.com/css2?family=Krona+One&family=Montserrat:wght@500;600&display=swap" rel="stylesheet">
<style>
  :root {
    --backdrop: #c3c3c3;
    --navy: #2f3d80;
    --navy-deep: #26336e;
    --gold: #f2c21b;
    --white: #ffffff;
    --band: #f4f4f4;
  }
  * { margin: 0; padding: 0; box-sizing: border-box; }
  html, body { width: 1200px; height: 781px; overflow: hidden; }
  body {
    background: var(--backdrop);
    position: relative;
    font-family: "Montserrat", Arial, sans-serif;
    color: var(--white);
  }
  .card {
    position: absolute;
    top: 242px;
    width: 520px;
    height: 297px;
    background: linear-gradient(160deg, var(--navy) 0%, var(--navy-deep) 100%);
    overflow: hidden;
    box-shadow: 0 10px 24px rgba(0,0,0,0.18);
  }
  .card--front { left: 50px; }
  .card--back { left: 630px; }

  .rule {
    position: absolute;
    height: 1.5px;
    background: var(--gold);
  }

  /* Front: person card */
  .front__rule-left { left: 0; top: 176px; width: 128px; }
  .front__rule-right { right: 0; top: 112px; width: 120px; }
  .identity {
    position: absolute;
    left: 140px;
    top: 86px;
    width: 250px;
  }
  .identity__firm {
    font-weight: 600;
    font-size: 8px;
    letter-spacing: 0.22em;
    margin-left: 4px;
    margin-bottom: 4px;
  }
  .identity__name {
    font-family: "Krona One", "Arial Black", sans-serif;
    font-size: 30px;
    line-height: 1.05;
    letter-spacing: 0.01em;
  }
  .contact {
    position: absolute;
    left: 32px;
    bottom: 34px;
    display: flex;
    gap: 26px;
    font-weight: 500;
    font-size: 11px;
    letter-spacing: 0.04em;
  }
  .contact__item { display: flex; align-items: center; gap: 7px; }
  .contact__icon { width: 15px; height: 15px; flex: none; }

  /* Back: firm card */
  .back__band { position: absolute; left: 0; top: 0; width: 520px; height: 40px; }
  .back__rule-left { left: 0; top: 176px; width: 66px; }
  .back__rule-right { right: 0; top: 110px; width: 66px; }
  .firm-mark {
    position: absolute;
    left: 82px;
    top: 118px;
    width: 356px;
    text-align: center;
    font-weight: 600;
    font-size: 27px;
    letter-spacing: 0.2em;
    white-space: nowrap;
  }
  .practice {
    position: absolute;
    left: 0;
    width: 520px;
    bottom: 52px;
    text-align: center;
    font-weight: 500;
    font-size: 10.5px;
    letter-spacing: 0.04em;
  }
  .practice__sep { color: var(--gold); margin: 0 4px; }
</style>
</head>
<body>

  <section class="card card--front" aria-label="Business card front">
    <span class="rule front__rule-left"></span>
    <span class="rule front__rule-right"></span>
    <div class="identity">
      <p class="identity__firm">OAK PARTNERS</p>
      <h1 class="identity__name">DORIAN<br>PEMBERTON</h1>
    </div>
    <div class="contact">
      <span class="contact__item">
        <svg class="contact__icon" viewBox="0 0 16 16" aria-hidden="true">
          <circle cx="8" cy="8" r="8" fill="var(--gold)"/>
          <path d="M5.2 4.2l1.6-.4.9 2.1-1 .8c.5 1.1 1.3 1.9 2.4 2.4l.8-1 2.1.9-.4 1.6c-3.6.1-6.5-2.8-6.4-6.4z" fill="var(--navy)"/>
        </svg>
        800-555-0147
      </span>
      <span class="contact__item">
        <svg class="contact__icon" viewBox="0 0 16 16" aria-hidden="true">
          <circle cx="8" cy="8" r="8" fill="var(--gold)"/>
          <rect x="4" y="5.2" width="8" height="5.6" fill="none" stroke="var(--navy)" stroke-width="1"/>
          <path d="M4 5.4l4 3 4-3" fill="none" stroke="var(--navy)" stroke-width="1"/>
        </svg>
        DORIAN@OAKPARTNERS.EXAMPLE
      </span>
    </div>
  </section>

  <section class="card card--back" aria-label="Business card back">
    <svg class="back__band" viewBox="0 0 520 40" aria-hidden="true">
      <polygon points="0,0 520,0 520,10 210,10 196,32 0,32" fill="var(--band)"/>
    </svg>
    <span class="rule back__rule-left"></span>
    <span class="rule back__rule-right"></span>
    <p class="firm-mark">OAK PARTNERS</p>
    <p class="practice">PERSONAL INJURY<span class="practice__sep">|</span>LEMON LAW<span class="practice__sep">|</span>WILDFIRE ATTORNEYS</p>
  </section>

</body>
</html>
```